Information security software developer needs new product website

We are Corvaxel - and we have created an anti-ransomware application that we think is pretty special.
Our product is now updating to version 2, bringing in a slew of new features that we want to showcase through this website.

The site itself should communicate trust and safety, be blue  (#22b8eb) and white and be themed around security, protection, shields and calmness. Due to the complex nature of the product, we will be creating a number of gifs to show usage of the features - the design needs to account for these gifs alongside feature headings.

Ideally, some graphics that communicate the themes of security and protection can be used throughout the design rather then technology photos - ultimately we don't want to scare people into using our product, we want it to feel like a trusted platform that makes sense to use.

you can read about us here - docs.corvaxel.io to get an idea of what we do!

```html
<!DOCTYPE html>
<html lang="en">
<head>
<meta charset="utf-8">
<title>Corvaxel Access Manager</title>
<link rel="stylesheet" href="https://fonts.googleapis.com/css2?family=Montserrat:wght@400;500;600&family=Roboto:wght@400;500&display=swap">
<style>
:root{
  --blue:#22b8eb;
  --blue-deep:#0b78c0;
  --dark:#2a2a2a;
  --slate:#7b8b95;
  --ink:#333;
  --muted:#8a8a8a;
  --white:#fff;
  --light:#f3f3f3;
  --navy:#0c1526;
}
*{box-sizing:border-box;margin:0;padding:0}
html,body{width:1200px;height:4209px;overflow:hidden}
body{position:relative;font-family:'Roboto',sans-serif;color:var(--ink);background:var(--white)}
.abs{position:absolute}
h1,h2,h3,.btn,.nav a{font-family:'Montserrat',sans-serif}
.btn{display:inline-block;background:var(--blue);color:var(--white);font-weight:500;font-size:16px;text-transform:uppercase;padding:0 27px;height:50px;line-height:50px;text-decoration:none;box-shadow:0 3px 8px rgba(0,0,0,.15)}
.photo{position:absolute}

/* top bar */
.topbar{left:0;top:0;width:1200px;height:42px;background:var(--dark)}
.social{display:flex;gap:9px;position:absolute;left:111px;top:9px}
.social span{width:25px;height:25px;border-radius:50%;background:var(--blue);display:block}
.contact{position:absolute;right:115px;top:0;line-height:42px;color:var(--white);font-family:'Montserrat',sans-serif;font-size:15px;display:flex;gap:22px}
.contact b{color:var(--blue);font-weight:400;margin-right:4px}

/* nav */
.header{left:0;top:42px;width:1200px;height:89px;background:var(--white)}
.brand{position:absolute;left:111px;top:16px;display:flex;align-items:center;gap:12px}
.brand i{width:56px;height:56px;background:var(--blue-deep);display:block}
.brand-text small{display:block;color:var(--blue-deep);font:600 13px 'Montserrat',sans-serif}
.brand-text span{font:500 21px 'Montserrat',sans-serif;color:#222}
.nav{position:absolute;right:112px;top:0;line-height:89px;display:flex;gap:24px}
.nav a{color:#444;text-decoration:none;font-size:16px}
.nav a.active{color:var(--blue)}

/* hero */
.hero{left:0;top:131px;width:1200px;height:651px;overflow:hidden}
.hero .photo{inset:0;background:linear-gradient(100deg,#5f6a72 0%,#8c9296 35%,#4b4e52 60%,#2d2f33 100%)}
.hero-title{left:107px;top:84px;font-size:44px;font-weight:500;color:var(--white)}
.hero-copy{left:111px;top:148px;width:530px;font-size:14.5px;line-height:27.5px;color:var(--white)}
.hero .btn{left:111px;top:246px}
.arrow{width:44px;height:44px;border:2px solid var(--white);border-radius:50%;top:287px}
.quote{background:var(--white);width:270px;height:101px;border-radius:4px;padding:14px 16px;box-shadow:0 2px 8px rgba(0,0,0,.2)}
.quote .who{display:flex;align-items:center;gap:8px;font-size:15px;color:#333}
.quote .who i{width:36px;height:36px;border-radius:50%;background:#b9a99b;display:block}
.quote p{font-size:11.5px;line-height:19px;color:var(--muted);margin-left:12px;margin-top:4px}

/* about */
.about-mark{left:134px;top:899px;width:410px;height:422px;display:flex;align-items:center;justify-content:center;gap:18px}
.about-mark i{width:70px;height:70px;background:var(--blue-deep);border-radius:10px;display:block}
.about-mark span{font:600 62px 'Montserrat',sans-serif;color:var(--blue-deep)}
.eyebrow{left:600px;top:851px;font:400 20px 'Montserrat',sans-serif;color:var(--blue)}
.about h2{left:597px;top:875px;font-size:38px;font-weight:500;color:#222;white-space:nowrap}
.about-copy{left:600px;top:952px;width:490px;font-size:13.5px;line-height:28px;color:#666}
.about-copy p{margin-bottom:14px}
.about .btn{left:600px;top:1278px}

/* defend band */
.band{left:0;top:1462px;width:1200px;height:418px;background:var(--slate)}
.band h2{left:108px;top:1492px;width:480px;font-size:33px;font-weight:500;line-height:37px;color:var(--white)}
.band-copy{left:111px;top:1622px;width:490px;font-size:13.5px;line-height:26px;color:var(--white)}
.band-copy p{margin-bottom:13px}
.band .btn{left:111px;top:1804px}
.band .photo{left:610px;top:1413px;width:494px;height:505px;background:radial-gradient(circle at 50% 45%,#1d3f55 0%,#0d2233 55%,#07141f 100%)}

/* features */
.section-title{width:1200px;left:0;text-align:center;font:500 42px 'Montserrat',sans-serif;color:var(--blue)}
.card{width:319px;height:435px;background:var(--white);box-shadow:0 1px 6px rgba(0,0,0,.12);border-radius:3px;overflow:hidden}
.card .photo{position:relative;height:222px;background:linear-gradient(135deg,#1b3d5c,#0c1f33)}
.card .photo.warm{background:linear-gradient(135deg,#8a8f96,#3a3e44)}
.card .photo.teal{background:linear-gradient(135deg,#15463f,#0b1f1d)}
.card-body{padding:22px 12px 0 12px}
.card h3{font-size:16px;font-weight:500;line-height:26px;color:#222;height:58px}
.card p{font-size:13px;line-height:25.5px;color:var(--muted);margin-top:12px;height:78px}
.card p em{font-style:normal;color:var(--blue)}
.more{display:block;margin-top:10px;font:500 14px 'Montserrat',sans-serif;color:var(--blue)}
.more::after{content:"";display:inline-block;width:10px;height:10px;border-radius:50%;background:var(--blue);margin-left:5px;vertical-align:-1px}

/* cta */
.cta{left:0;top:3041px;width:1200px;height:213px;background:linear-gradient(90deg,#0d1628,#101c30 50%,#0d1628)}
.cta h2{left:111px;top:3089px;font-size:23px;font-weight:500;color:var(--white)}
.cta-copy{left:113px;top:3138px;width:590px;font-size:13.5px;line-height:26px;color:#d8dde4}
.cta .btn{left:874px;top:3121px;font-size:15px;padding:0 20px}

/* news */
.news{background:linear-gradient(135deg,#1f5f9a,#0a2446)}
.news.lock{background:linear-gradient(135deg,#3a2a2a,#14202e 60%,#0d1724)}
.news.desk{background:linear-gradient(135deg,#b7a697,#5a6877)}
.date{position:absolute;left:12px;top:0;width:67px;height:67px;background:var(--blue);color:var(--white);text-align:center;font:500 15px/22px 'Montserrat',sans-serif;padding-top:10px}
.news-title{position:absolute;left:19px;font:500 14.5px/26px 'Montserrat',sans-serif;color:var(--white)}

/* partners */
.partners{left:0;top:3924px;width:1200px;height:131px;background:var(--light);display:flex;align-items:center;justify-content:space-between;padding:0 112px}
.partner{display:flex;align-items:center;gap:10px;font:500 32px 'Montserrat',sans-serif;color:#333}
.partner i{width:40px;height:40px;border-radius:50%;background:#222;display:block}

/* footer */
.footer{left:0;top:4055px;width:1200px;height:154px;background:var(--blue)}
.foot-brand{left:108px;top:4070px;display:flex;align-items:center;gap:12px;font:500 56px 'Montserrat',sans-serif;color:var(--white)}
.foot-brand i{width:44px;height:44px;background:var(--white);border-radius:6px;display:block}
.foot-social{left:111px;top:4142px;display:flex;gap:10px}
.foot-social span{width:12px;height:12px;border-radius:50%;background:var(--white);display:block}
.foot-nav{right:111px;top:4098px;display:flex;gap:24px}
.foot-nav a{color:var(--white);text-decoration:none;font:400 16px 'Montserrat',sans-serif}
.copyright{right:112px;top:4142px;color:var(--white);font-size:14px}
</style>
</head>
<body>

<div class="abs topbar">
  <div class="social"><span></span><span></span><span></span></div>
  <div class="contact"><span><b>✉</b>Email - info@corvaxel.com</span><span><b>✆</b>Call Now - 123-555-0148</span></div>
</div>

<header class="abs header">
  <div class="brand"><i></i><div class="brand-text"><small>Corvaxel</small><span>Access Manager</span></div></div>
  <nav class="nav"><a class="active" href="#">Home</a><a href="#">About</a><a href="#">Services</a><a href="#">Features</a><a href="#">News</a><a href="#">Contact</a></nav>
</header>

<section class="abs hero">
  <div class="photo" role="img" aria-label="Man with glasses working on a laptop in a bright city office"></div>
  <h1 class="abs hero-title">Corvaxel Access Manager</h1>
  <p class="abs hero-copy">Corvaxel Access Manager is a tool that allows you to safely delegate sensitive administrative access to computers in your DirectoryHub environment in a modern and user-friendly way</p>
  <a class="abs btn" href="#">Get Started</a>
  <svg class="abs arrow" style="left:16px" viewBox="0 0 44 44"><path d="M25 13 L16 22 L25 31" fill="none" stroke="#fff" stroke-width="2"/></svg>
  <svg class="abs arrow" style="left:1140px" viewBox="0 0 44 44"><path d="M19 13 L28 22 L19 31" fill="none" stroke="#fff" stroke-width="2"/></svg>
  <div class="abs quote" style="left:672px;top:345px"><div class="who"><i></i>Mara Delvin.</div><p>Lorem ipsum dolor sit amet, consectetur adipiscing elit, sed do eiusmod tempo</p></div>
  <div class="abs quote" style="left:868px;top:458px"><div class="who"><i></i>Mara Delvin.</div><p>Lorem ipsum dolor sit amet, consectetur adipiscing elit, sed do eiusmod tempo</p></div>
  <svg class="abs" style="left:0;top:551px" width="1200" height="100" viewBox="0 0 1200 100">
    <polygon points="0,6 1200,66 1200,100 0,100" fill="#22b8eb"/>
    <polygon points="0,100 1200,45 1200,100" fill="#fff"/>
  </svg>
</section>

<section class="about">
  <div class="abs about-mark"><i></i><span>Corvaxel</span></div>
  <div class="abs eyebrow">About</div>
  <h2 class="abs">Corvaxel Access Manager</h2>
  <div class="abs about-copy">
    <p>Lorem ipsum dolor sit amet, consectetur adipiscing elit, sed do eiusmod tempor incididunt ut labore et dolore magna aliqua. Ut enim ad minim veniam, quis nostrud exercitation ullamco laboris nisi ut aliquip</p>
    <p>Lorem ipsum dolor sit amet, consectetur adipiscing elit, sed do eiusmod tempor incididunt ut labore et dolore magna aliqua. Ut enim ad minim veniam, quis nostrud exercitation</p>
    <p>Lorem ipsum dolor sit amet, consectetur adipiscing elit, sed do eiusmod tempor incididunt ut labore et dolore magna aliqua. Ut enim ad minim veniam, quis nostrud exercitation ullamco laboris nisi ut aliquip ex ea commodo consequat. Duis aute irure dolor in reprehenderit</p>
  </div>
  <a class="abs btn" href="#">Read More</a>
</section>

<section>
  <div class="abs band"></div>
  <div class="band">
    <h2 class="abs">Defend against ransomware and other lateral movement-based attacks</h2>
    <div class="abs band-copy">
      <p>Corvaxel Access Manager is a tool that allows you to safely delegate sensitive administrative access to computers in your DirectoryHub environment in a modern and user-friendly way.</p>
      <p>It provides a web-based interface that allows users to request local admin passwords, DiskSeal recovery keys, and grant just-in-time administrative access to their own accounts.</p>
    </div>
    <a class="abs btn" href="#">Read More</a>
    <div class="photo" role="img" aria-label="Hooded figure facing screens of code in a dark blue room"></div>
  </div>
</section>

<h2 class="abs section-title" style="top:1990px">Features</h2>

<article class="abs card" style="left:111px;top:2063px">
  <div class="photo" role="img" aria-label="Laptop with a glowing padlock and hand holding a phone"></div>
  <div class="card-body"><h3>Web-based access to local admin passwords</h3><p>Access Manager provides a web-based and mobile-friendly interface for accessing local admin passwords.</p><a class="more">Read More</a></div>
</article>
<article class="abs card" style="left:441px;top:2063px">
  <div class="photo warm" role="img" aria-label="Hands typing on a laptop with a padlock overlay"></div>
  <div class="card-body"><h3>Access historical local admin passwords</h3><p>Deploying the Corvaxel Access Manager Agent to your fleet allows you to upgrade to encrypted local admin passwords</p><a class="more">Read More</a></div>
</article>
<article class="abs card" style="left:772px;top:2063px">
  <div class="photo warm" role="img" aria-label="Laptop with floating security and home icons"></div>
  <div class="card-body"><h3>Just-in-time administrative access to computers</h3><p>Using the same web interface,request that their account be added to a group that is a member of the local administrators</p><a class="more">Read More</a></div>
</article>
<article class="abs card" style="left:111px;top:2518px">
  <div class="photo teal" role="img" aria-label="Two engineers with a laptop in a server room"></div>
  <div class="card-body"><h3>Easy access to DiskSeal recovery passwords</h3><p>Authorized users can also request DiskSeal recovery passwords for a computer through the same easy-to-use web interface.</p><a class="more">Read More</a></div>
</article>
<article class="abs card" style="left:441px;top:2518px">
  <div class="photo" role="img" aria-label="Analyst at a desk with several monitors"></div>
  <div class="card-body"><h3>Audit success and failure event logs</h3><p>All success and failure events are logged to the system event log and a file. Optionally, you can send audit events via email,</p><a class="more">Read More</a></div>
</article>
<article class="abs card" style="left:772px;top:2518px">
  <div class="photo" role="img" aria-label="Operators in a blue-lit control room"></div>
  <div class="card-body"><h3>Modern authentication options</h3><p>The web app supports traditional system authentication, as well as authentication providers such as <em>FedAuth</em> or 3rd party</p><a class="more">Read More</a></div>
</article>

<section>
  <div class="abs cta" role="img" aria-label="Dark navy band with faint red padlock pattern"></div>
  <div class="cta">
    <h2 class="abs">Lorem ipsum dolor sit amet, consectetur adipiscing</h2>
    <p class="abs cta-copy">Lorem ipsum dolor sit amet, consectetur adipiscing elit, sed do eiusmod tempor incididunt ut labore et dolore magna aliqua. Ut enim ad minim veniam,</p>
    <a class="abs btn" href="#">Download The App</a>
  </div>
</section>

<h2 class="abs section-title" style="top:3327px">Our Latest News</h2>

<article class="abs news" style="left:121px;top:3417px;width:471px;height:429px" role="img" aria-label="Glowing cloud with a keyhole over a digital globe">
  <div class="date">May<br>28</div>
  <div class="news-title" style="top:364px">Lorem ipsum dolor sit amet, consectetur adipiscing elit,<br>sed do eiusmod tempor</div>
</article>
<article class="abs news lock" style="left:610px;top:3417px;width:471px;height:208px" role="img" aria-label="Hand touching a glowing padlock icon">
  <div class="date">May<br>28</div>
  <div class="news-title" style="top:169px">Lorem ipsum dolor sit amet, consectetur adipiscing elit,</div>
</article>
<article class="abs news desk" style="left:610px;top:3638px;width:471px;height:208px" role="img" aria-label="Person at a laptop showing a secure access screen">
  <div class="date">May<br>28</div>
  <div class="news-title" style="top:169px">Lorem ipsum dolor sit amet, consectetur adipiscing elit,</div>
</article>

<div class="abs partners">
  <div class="partner"><i></i>Orbitly</div>
  <div class="partner">Fennix</div>
  <div class="partner">Quarra</div>
  <div class="partner">Nodewell</div>
  <div class="partner">Pylora</div>
</div>

<footer>
  <div class="abs footer"></div>
  <div class="abs foot-brand"><i></i>Corvaxel</div>
  <div class="abs foot-social"><span></span><span></span><span></span></div>
  <nav class="abs foot-nav"><a href="#">Home</a><a href="#">About</a><a href="#">Services</a><a href="#">Features</a><a href="#">News</a><a href="#">Contact</a></nav>
  <div class="abs copyright">© 2021 All Rights Reserved</div>
</footer>

</body>
</html>
```